Business card design for Automotive workshop

We need a business card for a new automotive repair and tyre shop called Keelstone Prime Automotive located in New Zealand. We are a clean, modern and fresh workshop and company.

Front needs to feature logo,
my name:
Marlo Fenwicke (director)

Address:
48 Tarn Lane
Whitianga 3510

Phone: 07 594 2713
Mobile: 027 451 9362
Email: office@keelstoneautomotive.example.nz
Website: keelstoneautomotive.example.nz

Back needs to feature an area to write down appointment details, date and time.

Also feature a list of jobs and work we do such as,
Vehicle Servicing
All Mechanical Repairs
Warrant of Fitness
Tyres & Wheel Alignments
Automotive Diagnostics
Automotive Parts & Supplies

```html
<!DOCTYPE html>
<html lang="en">
<head>
<meta charset="utf-8">
<title>Keelstone Prime Automotive – Business Card</title>
<link rel="stylesheet" href="https://fonts.googleapis.com/css2?family=Exo+2:wght@400;500;700&family=Open+Sans:wght@600;700&display=swap">
<style>
  :root {
    --red: #e31b23;
    --black: #0d0d0d;
    --charcoal: #2a2a2a;
    --white: #ffffff;
    --stage: #6b727c;
    --rule: #555555;
  }
  * { box-sizing: border-box; margin: 0; padding: 0; }
  html, body { width: 1200px; height: 900px; overflow: hidden; }
  body {
    background: var(--stage);
    display: flex;
    flex-direction: column;
    align-items: center;
    justify-content: center;
    gap: 44px;
    font-family: "Exo 2", sans-serif;
  }
  .card {
    position: relative;
    width: 620px;
    height: 370px;
    overflow: hidden;
    box-shadow: 0 6px 18px rgba(0,0,0,.35);
  }

  /* Back */
  .card--back { background: var(--black); color: var(--white); }
  .back-texture {
    position: absolute; inset: 0;
    background: radial-gradient(ellipse at 45% 40%, #3a3a3a 0%, #1a1a1a 45%, #080808 100%);
  }
  .back-logo {
    position: absolute; left: 34px; top: 118px;
    font-family: "Exo 2", sans-serif; font-weight: 700;
    font-size: 23px; color: var(--red); letter-spacing: .5px;
  }
  .services {
    position: absolute; left: 360px; top: 26px;
    font-family: "Open Sans", sans-serif; font-weight: 600;
    font-size: 12.5px; line-height: 1.55;
  }
  .services__title { color: var(--red); font-weight: 700; font-size: 14px; letter-spacing: .3px; }
  .services ul { list-style: none; }
  .services li { position: relative; padding-left: 14px; }
  .services li::before {
    content: ""; position: absolute; left: 2px; top: 8px;
    width: 5px; height: 5px; border-radius: 50%; background: var(--red);
  }
  .appointment {
    position: absolute; left: 0; right: 0; bottom: 0; height: 150px;
    background: var(--white);
    padding: 34px 36px 0;
    display: flex; flex-direction: column; gap: 30px;
  }
  .appointment__row { display: flex; align-items: flex-end; gap: 8px; font-family: "Open Sans", sans-serif; font-weight: 600; font-size: 14px; color: var(--red); }
  .appointment__line { flex: 1; border-bottom: 1.5px dotted var(--rule); height: 1px; margin-bottom: 4px; }
  .appointment__line--date { flex: 1.5; }

  /* Front */
  .card--front { background: var(--white); }
  .front-logo {
    position: absolute; left: 0; right: 0; top: 82px;
    text-align: center;
    font-weight: 700; font-size: 34px; color: var(--red); letter-spacing: .5px;
  }
  .person {
    position: absolute; left: 0; bottom: 0; width: 320px; height: 138px;
    background: var(--black); color: var(--white);
    padding: 18px 0 0 30px;
  }
  .person__name { font-size: 21px; font-weight: 500; letter-spacing: .4px; }
  .person__role { font-size: 13px; margin-top: 1px; margin-left: 2px; }
  .person__address { font-size: 14px; margin-top: 14px; line-height: 1.3; letter-spacing: .3px; }
  .contact {
    position: absolute; right: 0; bottom: 0; left: 324px; height: 112px;
    background: var(--red); color: var(--white);
    padding: 12px 22px 0 0;
    display: flex; flex-direction: column; align-items: flex-end; gap: 2px;
  }
  .contact__item { display: flex; align-items: center; gap: 10px; font-size: 12.5px; letter-spacing: .3px; }
  .contact__item--phone { font-size: 15px; }
  .contact__icon { width: 14px; height: 14px; flex: none; }
</style>
</head>
<body>

  <section class="card card--back" aria-label="Card back">
    <div class="back-texture" role="img" aria-label="Dark textured carbon background"></div>
    <div class="back-logo">Keelstone Prime Automotive</div>
    <div class="services">
      <p class="services__title">VEHICLE SERVICING</p>
      <ul>
        <li>All Mechanical Repairs</li>
        <li>Warrant of Fitness</li>
        <li>Tyres &amp; Wheel Alignments</li>
        <li>Automotive Diagnostics</li>
        <li>Automotive Parts &amp; Supplies</li>
      </ul>
    </div>
    <div class="appointment">
      <div class="appointment__row"><span>Date:</span><span class="appointment__line appointment__line--date"></span><span>Time:</span><span class="appointment__line"></span></div>
      <div class="appointment__row"><span>Date:</span><span class="appointment__line appointment__line--date"></span><span>Time:</span><span class="appointment__line"></span></div>
    </div>
  </section>

  <section class="card card--front" aria-label="Card front">
    <div class="front-logo">Keelstone Prime Automotive</div>
    <div class="person">
      <p class="person__name">Marlo Fenwicke</p>
      <p class="person__role">Director</p>
      <p class="person__address">48 Tarn Lane<br>Whitianga 3510</p>
    </div>
    <div class="contact">
      <p class="contact__item contact__item--phone">07 594 2713
        <svg class="contact__icon" viewBox="0 0 24 24"><path fill="#fff" d="M6.6 10.8a15.1 15.1 0 0 0 6.6 6.6l2.2-2.2c.3-.3.7-.4 1-.2 1.1.4 2.3.6 3.6.6.6 0 1 .4 1 1V20c0 .6-.4 1-1 1A17 17 0 0 1 3 4c0-.6.4-1 1-1h3.5c.6 0 1 .4 1 1 0 1.3.2 2.5.6 3.6.1.3 0 .7-.2 1z"/></svg>
      </p>
      <p class="contact__item contact__item--phone">027 451 9362
        <svg class="contact__icon" viewBox="0 0 24 24"><rect x="6" y="2" width="12" height="20" rx="2" fill="none" stroke="#fff" stroke-width="2.4"/><circle cx="12" cy="18" r="1.3" fill="#fff"/></svg>
      </p>
      <p class="contact__item">office@keelstoneautomotive.example.nz
        <svg class="contact__icon" viewBox="0 0 24 24"><rect x="2" y="5" width="20" height="14" fill="#fff"/><path d="M2 5l10 8 10-8" fill="none" stroke="#e31b23" stroke-width="1.6"/></svg>
      </p>
      <p class="contact__item">www.keelstoneautomotive.example.nz
        <svg class="contact__icon" viewBox="0 0 24 24"><circle cx="12" cy="12" r="10" fill="none" stroke="#fff" stroke-width="2"/><ellipse cx="12" cy="12" rx="4" ry="10" fill="none" stroke="#fff" stroke-width="1.6"/><path d="M2 12h20" stroke="#fff" stroke-width="1.6"/></svg>
      </p>
    </div>
  </section>

</body>
</html>
```